KVOR Individual and Corporate Development Business Card Design

KVOR needs a business card design that is aligned with it's values and targetted markets. Coherent Lattice of Adaptive Reasoning Method's self diagnosis model and tools, which can be used for personal improvement and team/business performance enhancement, is based on the learnings of over 20 years of medical practitioning. KVOR supercharges personal effectiveness and awareness to also increase team and business performance.

The targetted markets are high performance individuals and teams who aspire seek to enhance their capabilities and achieve their absolute best potential.

Look and feel for the business card design we are looking for is high technology, premium, fresh, new and medical.

Target Market(s)

Industry/Entity Type

Business Consultant

Contact Information for Business Card

Logo, Full Name, Title, Phone number, Email, company name, Address,

Font styles to use
Sans Serif

Requirements
Must have
• Tag line: Elevating Potential for Ambitious High Achievers
• Please use same colours as the logo.

```html
<!DOCTYPE html>
<html lang="en">
<head>
<meta charset="utf-8">
<title>KVOR Business Cards</title>
<link rel="stylesheet" href="https://fonts.googleapis.com/css2?family=Roboto+Condensed:wght@400;500;700&family=Roboto:ital,wght@0,400;1,400&display=swap">
<style>
  :root {
    --teal: #00a9c3;
    --charcoal: #5a5d63;
    --edge: #55585d;
    --paper: #f4f4f4;
    --white: #ffffff;
    --backdrop: #2a2a2a;
    --rule-light: #c9cbcd;
    --rule-dark: #8b8e93;
  }
  * { margin: 0; padding: 0; box-sizing: border-box; }
  html, body { width: 1200px; height: 724px; overflow: hidden; }
  body { background: var(--backdrop); position: relative; font-family: "Roboto", Arial, sans-serif; }

  .card {
    position: absolute; width: 529px; height: 302px; overflow: hidden;
    box-shadow: 0 3px 8px rgba(0,0,0,0.55);
  }
  .card--tl { left: 62px; top: 41px; }
  .card--tr { left: 619px; top: 41px; }
  .card--bl { left: 62px; top: 371px; }
  .card--br { left: 619px; top: 371px; background: var(--charcoal); }

  .card__bg { position: absolute; inset: 0; width: 100%; height: 100%; }

  .holder { position: absolute; left: 29px; color: var(--white); font-family: "Roboto Condensed", Arial, sans-serif; }
  .holder--two-line { top: 88px; }
  .holder--three-line { top: 66px; }
  .holder__name { font-size: 18px; font-weight: 500; text-transform: uppercase; line-height: 22px; }
  .holder__degree { font-size: 15px; font-weight: 500; text-transform: uppercase; line-height: 22px; }
  .holder__role { font-size: 14px; font-weight: 400; text-transform: uppercase; line-height: 22px; }

  .contact { position: absolute; left: 29px; top: 180px; list-style: none; color: var(--white); font-size: 12.5px; }
  .contact li { display: flex; align-items: center; height: 17px; }
  .contact svg { width: 11px; height: 11px; margin-right: 7px; fill: var(--white); }

  .brand { position: absolute; left: 290px; top: 106px; width: 210px; text-align: center;
           font-family: "Roboto Condensed", Arial, sans-serif; font-weight: 700; color: var(--teal); }
  .brand__name { font-size: 44px; line-height: 44px; letter-spacing: 3px; display: flex; align-items: center; justify-content: center; gap: 10px; }
  .brand__dot { width: 12px; height: 12px; border-radius: 50%; background: var(--teal); }
  .brand__rule { height: 2px; background: var(--rule-light); margin: 6px 0 4px; }
  .brand__full { font-size: 11px; line-height: 13px; text-transform: uppercase; letter-spacing: 0.3px; }

  .brand--reverse { left: 120px; top: 118px; width: 290px; color: var(--white); }
  .brand--reverse .brand__name { font-size: 58px; line-height: 58px; }
  .brand--reverse .brand__dot { background: var(--white); width: 15px; height: 15px; }
  .brand--reverse .brand__rule { background: var(--rule-dark); }
  .brand--reverse .brand__full { font-size: 14px; line-height: 17px; }

  .tagline { position: absolute; left: 0; right: 0; top: 258px; text-align: center; color: var(--white);
             font-style: italic; font-size: 12.5px; }
</style>
</head>
<body>

<svg width="0" height="0" style="position:absolute">
  <defs>
    <symbol id="card-face" viewBox="0 0 600 342">
      <rect width="600" height="342" fill="var(--teal)"/>
      <path d="M388 0 H600 V342 H388 L252 196 Q238 171 252 150 Z" fill="var(--edge)"/>
      <path d="M395 0 H600 V342 H395 L259 196 Q245 171 259 150 Z" fill="var(--white)"/>
      <path d="M403 0 H600 V342 H403 L267 196 Q253 171 267 150 Z" fill="var(--paper)"/>
    </symbol>
    <symbol id="icon-phone" viewBox="0 0 12 12"><path d="M2.5 0.5 L4.5 0.5 L5.2 3.4 L3.8 4.5 Q5 7 7.5 8.2 L8.6 6.8 L11.5 7.5 L11.5 9.5 Q11 11.5 9 11.5 Q1 10.5 0.5 3 Q0.5 1 2.5 0.5 Z"/></symbol>
    <symbol id="icon-mail" viewBox="0 0 12 12"><path d="M0.5 2.5 H11.5 V9.5 H0.5 Z M1.2 3.2 L6 6.5 L10.8 3.2" /></symbol>
    <symbol id="icon-web" viewBox="0 0 12 12"><circle cx="6" cy="6" r="5.5"/></symbol>
  </defs>
</svg>

<article class="card card--tl">
  <svg class="card__bg" preserveAspectRatio="none"><use href="#card-face"/></svg>
  <div class="holder holder--two-line">
    <p class="holder__name">Dr Helena Marsh</p>
    <p class="holder__role">Managing Director</p>
  </div>
  <ul class="contact">
    <li><svg><use href="#icon-phone"/></svg>+61 402 318 570</li>
    <li><svg><use href="#icon-mail"/></svg>helena.marsh@kvor.com.au</li>
    <li><svg><use href="#icon-web"/></svg>www.kvor.com.au</li>
  </ul>
  <div class="brand">
    <p class="brand__name"><span class="brand__dot"></span>KVOR</p>
    <div class="brand__rule"></div>
    <p class="brand__full">Coherent Lattice of Adaptive<br>Reasoning Method</p>
  </div>
</article>

<article class="card card--tr">
  <svg class="card__bg" preserveAspectRatio="none"><use href="#card-face"/></svg>
  <div class="holder holder--three-line">
    <p class="holder__name">Owen Tasker</p>
    <p class="holder__degree">B. Eng (Hons)/B. Bus</p>
    <p class="holder__role">Director</p>
  </div>
  <ul class="contact">
    <li><svg><use href="#icon-phone"/></svg>+61 413 627 094</li>
    <li><svg><use href="#icon-mail"/></svg>owen.tasker@kvor.com.au</li>
    <li><svg><use href="#icon-web"/></svg>www.kvor.com.au</li>
  </ul>
  <div class="brand">
    <p class="brand__name"><span class="brand__dot"></span>KVOR</p>
    <div class="brand__rule"></div>
    <p class="brand__full">Coherent Lattice of Adaptive<br>Reasoning Method</p>
  </div>
</article>

<article class="card card--bl">
  <svg class="card__bg" preserveAspectRatio="none"><use href="#card-face"/></svg>
  <div class="holder holder--two-line">
    <p class="holder__name">Julian Ferraro (PhD)</p>
    <p class="holder__role">Director</p>
  </div>
  <ul class="contact">
    <li><svg><use href="#icon-phone"/></svg>+61 481 536 212</li>
    <li><svg><use href="#icon-mail"/></svg>julian.ferraro@kvor.com.au</li>
    <li><svg><use href="#icon-web"/></svg>www.kvor.com.au</li>
  </ul>
  <div class="brand">
    <p class="brand__name"><span class="brand__dot"></span>KVOR</p>
    <div class="brand__rule"></div>
    <p class="brand__full">Coherent Lattice of Adaptive<br>Reasoning Method</p>
  </div>
</article>

<article class="card card--br">
  <div class="brand brand--reverse">
    <p class="brand__name"><span class="brand__dot"></span>KVOR</p>
    <div class="brand__rule"></div>
    <p class="brand__full">Coherent Lattice of Adaptive<br>Reasoning Method</p>
  </div>
  <p class="tagline">Elevating Potential for Ambitious High Achievers</p>
</article>

</body>
</html>
```